Business Card Design

We need a business card designed for our new company. Prefer a black card with white logo & writing.

Contact Information for Business Card

Ted Galloway, address: 7-4812 Fernhollow Road, Abbotsford, BC, V3K 8R2, Office Phone: 604-712-3390, Cell: 604-947-2164, Email: ted@resinworkshub.ca

Colors

Designer to choose only greyscale colors for use in the design.

```html
<!DOCTYPE html>
<html lang="en">
<head>
<meta charset="utf-8">
<title>Resin Works Hub – Business Card</title>
<link rel="stylesheet" href="https://fonts.googleapis.com/css2?family=Montserrat:wght@400;600;700;800&display=swap">
<style>
  :root {
    --backdrop: #d9d6d2;
    --card: #222222;
    --card-edge: #1a1a1a;
    --ink: #ffffff;
    --ink-soft: #e6e6e6;
    --pattern-light: #3c3c3c;
    --pattern-dark: #0e0e0e;
  }
  * { margin: 0; padding: 0; box-sizing: border-box; }
  html, body { width: 900px; height: 1200px; overflow: hidden; background: var(--backdrop); }
  .canvas { position: relative; width: 900px; height: 1200px; font-family: "Montserrat", sans-serif; color: var(--ink); }

  .card {
    position: absolute; left: 80px; width: 742px; height: 442px;
    border-radius: 22px; background: var(--card);
    box-shadow: 0 6px 18px rgba(0,0,0,0.35);
    overflow: hidden;
  }
  .card-front { top: 130px; }
  .card-back { top: 638px; height: 440px; }

  .brand-mark {
    position: absolute; left: 100px; top: 200px; width: 250px;
    text-align: center; font-weight: 800; color: var(--ink); line-height: 1;
  }
  .brand-mark .brand-main { display: block; font-size: 36px; letter-spacing: 0.5px; }
  .brand-mark .brand-sub { display: block; font-size: 22px; letter-spacing: 6px; margin-top: 10px; }

  .divider { position: absolute; left: 370px; top: 128px; width: 3px; height: 222px; background: var(--ink); }

  .contact { position: absolute; left: 392px; top: 122px; }
  .contact-name { font-size: 25px; font-weight: 700; line-height: 1.2; }
  .contact-role { font-size: 15px; font-weight: 400; color: var(--ink-soft); margin-top: 8px; }
  .contact-address { font-size: 16px; line-height: 21px; margin-top: 14px; color: var(--ink-soft); }
  .contact-list { list-style: none; margin-top: 16px; }
  .contact-list li { display: flex; align-items: center; gap: 12px; font-size: 16px; color: var(--ink-soft); height: 27px; }
  .contact-list li:nth-child(2) { height: 30px; }
  .contact-list svg { width: 16px; height: 16px; flex: none; fill: var(--ink); }

  .back-pattern {
    position: absolute; inset: 0;
    background: linear-gradient(125deg, var(--pattern-light) 0%, #262626 40%, var(--pattern-dark) 100%);
  }
  .back-mark {
    position: absolute; left: 492px; top: 306px; width: 130px;
    text-align: center; font-weight: 800; color: var(--ink); line-height: 1;
  }
  .back-mark .brand-main { display: block; font-size: 15px; }
  .back-mark .brand-sub { display: block; font-size: 10px; letter-spacing: 3px; margin-top: 5px; }
</style>
</head>
<body>
<main class="canvas">

  <section class="card card-front" aria-label="Card front">
    <div class="brand-mark">
      <span class="brand-main">RESIN WORKS</span>
      <span class="brand-sub">HUB</span>
    </div>

    <div class="divider"></div>

    <div class="contact">
      <h1 class="contact-name">Ted Galloway</h1>
      <p class="contact-role">owner</p>
      <p class="contact-address">7-4812 Fernhollow Road,<br>Abbotsford, BC, V3K 8R2</p>
      <ul class="contact-list">
        <li>
          <svg viewBox="0 0 24 24" aria-hidden="true"><path d="M6.6 10.8a15.1 15.1 0 0 0 6.6 6.6l2.2-2.2a1 1 0 0 1 1-.25 11.4 11.4 0 0 0 3.6.57 1 1 0 0 1 1 1V20a1 1 0 0 1-1 1A17 17 0 0 1 3 4a1 1 0 0 1 1-1h3.5a1 1 0 0 1 1 1c0 1.25.2 2.45.57 3.6a1 1 0 0 1-.25 1z"/></svg>
          604-712-3390
        </li>
        <li>
          <svg viewBox="0 0 24 24" aria-hidden="true"><path d="M7 1h10a2 2 0 0 1 2 2v18a2 2 0 0 1-2 2H7a2 2 0 0 1-2-2V3a2 2 0 0 1 2-2zm0 3v15h10V4zm5 16.2a1 1 0 1 0 0 2 1 1 0 0 0 0-2z"/></svg>
          604-947-2164
        </li>
        <li>
          <svg viewBox="0 0 24 24" aria-hidden="true"><path d="M2 5h20v14H2zm2 2v.4l8 5.2 8-5.2V7zm0 2.8V17h16V9.8l-8 5.2z"/></svg>
          ted@resinworkshub.ca
        </li>
        <li>
          <svg viewBox="0 0 24 24" aria-hidden="true"><path d="M12 2a10 10 0 1 0 0 20 10 10 0 0 0 0-20zm-1 17.9A8 8 0 0 1 4.1 10L9 15v1a2 2 0 0 0 2 2zm6.9-2.5A2 2 0 0 0 16 16h-1v-3a1 1 0 0 0-1-1H8v-2h2a1 1 0 0 0 1-1V7h2a2 2 0 0 0 2-2v-.4a8 8 0 0 1 2.9 12.8z"/></svg>
          www.resinworkshub.ca
        </li>
      </ul>
    </div>
  </section>

  <section class="card card-back" aria-label="Card back">
    <div class="back-pattern" role="img" aria-label="Tonal repeating brand pattern fading from grey to black"></div>
    <div class="back-mark">
      <span class="brand-main">RESIN WORKS</span>
      <span class="brand-sub">HUB</span>
    </div>
  </section>

</main>
</body>
</html>
```